Bramblewood Card Company Business Cards

We are a trading card store with Glimmorax, sports and other TCG cards, we need a business card design that encompasses a clean cut, modern style with a retro flare. website is bramblewoodcardco.com for reference. Can utilize a comic book era feel or a more modern outdoor feel to utilize the "Pacific Northwest" elements of tress, mountains, etc.

Industry/Entity Type

Trading cards and collectibles

Contact Information for Business Card

business name, email address, phone number, name, owner job title

Font styles to use
Sans Serif

```html
<!DOCTYPE html>
<html lang="en">
<head>
<meta charset="utf-8">
<title>Bramblewood Card Company — Business Cards</title>
<link rel="stylesheet" href="https://fonts.googleapis.com/css2?family=Montserrat:wght@500;700;800&family=Open+Sans:wght@400;600&display=swap">
<style>
  :root {
    --stage: #3d3d3d;
    --card-white: #ffffff;
    --card-dark: #2b2b2b;
    --slate: #6b6b6b;
    --ink: #333333;
    --cyan: #12b8dc;
    --muted: #6f6f6f;
  }
  * { box-sizing: border-box; margin: 0; padding: 0; }
  html, body {
    width: 1200px; height: 803px; overflow: hidden;
    background: var(--stage);
  }
  .stage {
    position: relative; width: 1200px; height: 803px;
    display: flex; align-items: center; justify-content: center; gap: 50px;
  }
  .card {
    position: relative; width: 520px; height: 297px;
    border-radius: 22px;
    border-bottom: 4px solid var(--cyan);
    box-shadow: 0 18px 34px rgba(0,0,0,.35);
    overflow: hidden;
  }
  .card--front { background: var(--card-white); }
  .card--back { background: var(--card-dark); display: flex; align-items: center; justify-content: center; }

  .brand {
    display: flex; align-items: center; gap: 12px;
  }
  .brand__mark {
    width: 16px; height: 16px; border-radius: 50%;
    background: var(--cyan); flex: none;
  }
  .brand__name {
    font-family: "Montserrat", sans-serif; font-weight: 800;
    text-transform: uppercase; letter-spacing: .06em; line-height: 1.15;
    color: var(--slate);
  }
  .card--front .brand { position: absolute; left: 44px; top: 52px; }
  .card--front .brand__name { font-size: 20px; width: 260px; }
  .card--back .brand__name { font-size: 30px; width: 330px; text-align: center; }
  .card--back .brand__mark { width: 22px; height: 22px; }

  .person { position: absolute; left: 44px; top: 150px; }
  .person__name {
    font-family: "Montserrat", sans-serif; font-weight: 700;
    font-size: 28px; color: var(--cyan); line-height: 1.1;
  }
  .person__title {
    font-family: "Open Sans", sans-serif; font-size: 13px; color: var(--muted);
    margin-top: 2px;
  }
  .contact { list-style: none; margin-top: 14px; }
  .contact__item {
    display: flex; align-items: center; gap: 8px;
    font-family: "Open Sans", sans-serif; font-size: 13px; color: var(--ink);
    line-height: 1.6;
  }
  .contact__icon { width: 12px; height: 12px; fill: var(--cyan); flex: none; }
</style>
</head>
<body>
<main class="stage">
  <section class="card card--front" aria-label="Business card front">
    <div class="brand">
      <span class="brand__mark"></span>
      <span class="brand__name">Bramblewood Card Company</span>
    </div>
    <div class="person">
      <h1 class="person__name">Owen Hartley</h1>
      <p class="person__title">President</p>
      <ul class="contact">
        <li class="contact__item">
          <svg class="contact__icon" viewBox="0 0 24 24" aria-hidden="true"><path d="M6.6 10.8a15 15 0 0 0 6.6 6.6l2.2-2.2a1 1 0 0 1 1-.25 11.4 11.4 0 0 0 3.6.6 1 1 0 0 1 1 1V20a1 1 0 0 1-1 1A17 17 0 0 1 3 4a1 1 0 0 1 1-1h3.5a1 1 0 0 1 1 1c0 1.25.2 2.45.6 3.6a1 1 0 0 1-.25 1z"/></svg>
          555-014-2290
        </li>
        <li class="contact__item">
          <svg class="contact__icon" viewBox="0 0 24 24" aria-hidden="true"><path d="M2 5h20v14H2z M3.5 6.5 12 13l8.5-6.5" fill="var(--cyan)"/><path d="M3.5 6.5 12 13l8.5-6.5" fill="none" stroke="#fff" stroke-width="1.6"/></svg>
          info@bramblewoodcardco.com
        </li>
        <li class="contact__item">
          <svg class="contact__icon" viewBox="0 0 24 24" aria-hidden="true"><circle cx="12" cy="12" r="10"/><path d="M2 12h20M12 2c3 3 3 17 0 20M12 2c-3 3-3 17 0 20" fill="none" stroke="#fff" stroke-width="1.4"/></svg>
          www.bramblewoodcardco.com
        </li>
      </ul>
    </div>
  </section>

  <section class="card card--back" aria-label="Business card back">
    <div class="brand">
      <span class="brand__mark"></span>
      <span class="brand__name">Bramblewood Card Company</span>
    </div>
  </section>
</main>
</body>
</html>
```